Oriel Photography Business Card

I need a business card designed for a photography business based in Perth, Western Australia called Oriel Photography.

We specialise in wedding, event photography and portrait photography.

The business card must borrow the style of the attached logo.

The hex codes for the colours in the logo are:
#ED1D85 - Pink
#89C23E - Green
#37282F - Black

The name on the card will be:
Name: Tobrian
Phone: 0417395268
Website: www.orielphotography.example.com.au
Facebook: orielphotography

I am open and happy to accept creative concepts.

I’d like some space at the back for writing notes and appointment details.

```html
<!DOCTYPE html>
<html lang="en">
<head>
<meta charset="utf-8">
<title>Oriel Photography Business Card</title>
<link rel="stylesheet" href="https://fonts.googleapis.com/css2?family=Open+Sans:wght@400;700&family=Questrial&display=swap">
<style>
  :root {
    --pink: #ED1D85;
    --green: #89C23E;
    --ink: #37282F;
    --text: #222222;
    --rule: #7a7a80;
    --panel: #f3f4f6;
    --panel-edge: #e2e3e6;
    --card: #ffffff;
    --backdrop: #dfe4e3;
  }
  * { margin: 0; padding: 0; box-sizing: border-box; }
  html, body { width: 1200px; height: 900px; overflow: hidden; }
  body { background: var(--backdrop); position: relative; font-family: "Open Sans", Arial, sans-serif; }

  .card {
    position: absolute;
    width: 648px;
    height: 352px;
    background: var(--card);
    overflow: hidden;
  }
  .card--front { left: 34px; top: 88px; }
  .card--back { left: 500px; top: 372px; }

  .brand-panel {
    position: absolute;
    left: 258px;
    width: 138px;
    background: var(--panel);
    border-left: 1px solid var(--panel-edge);
    border-right: 1px solid var(--panel-edge);
    border-bottom: 1px solid var(--panel-edge);
    display: flex;
    align-items: center;
    justify-content: center;
  }
  .card--front .brand-panel { top: 0; height: 126px; }
  .card--back .brand-panel--top { top: 0; height: 183px; }
  .card--back .brand-panel--bottom { top: 244px; height: 108px; border-top: 1px solid var(--panel-edge); border-bottom: none; }

  .brand-dot { width: 58px; height: 58px; border-radius: 50%; background: var(--pink); }
  .card--back .brand-dot { width: 66px; height: 66px; }

  .wordmark {
    position: absolute;
    left: 0; right: 0;
    text-align: center;
    font-family: "Questrial", Arial, sans-serif;
    color: var(--ink);
    text-transform: uppercase;
    white-space: nowrap;
  }
  .card--front .wordmark { top: 138px; font-size: 14px; letter-spacing: 0.52em; padding-left: 10px; }
  .card--back .wordmark { top: 203px; font-size: 16px; letter-spacing: 0.62em; padding-left: 12px; }

  .contact { position: absolute; left: 32px; top: 209px; color: var(--text); }
  .contact__name { color: var(--pink); font-weight: 700; font-size: 20px; line-height: 1; margin-bottom: 24px; }
  .contact__line { font-size: 16.5px; line-height: 22px; }

  .notes { position: absolute; left: 354px; top: 253px; width: 294px; }
  .notes__line { height: 17.5px; border-top: 1.5px solid var(--rule); }
</style>
</head>
<body>
  <section class="card card--front" aria-label="Business card front">
    <div class="brand-panel"><span class="brand-dot"></span></div>
    <div class="wordmark">Oriel Photography</div>
    <div class="contact">
      <p class="contact__name">Tobrian</p>
      <p class="contact__line">Phone: 0417395268</p>
      <p class="contact__line">www.orielphotography.example.com.au</p>
      <p class="contact__line">Facebook: orielphotography</p>
    </div>
    <div class="notes" aria-label="Lines for notes">
      <div class="notes__line"></div>
      <div class="notes__line"></div>
      <div class="notes__line"></div>
      <div class="notes__line"></div>
      <div class="notes__line"></div>
    </div>
  </section>

  <section class="card card--back" aria-label="Business card back">
    <div class="brand-panel brand-panel--top"><span class="brand-dot"></span></div>
    <div class="wordmark">Oriel Photography</div>
    <div class="brand-panel brand-panel--bottom"></div>
  </section>
</body>
</html>
```